New business card for a regional office of a US M&A company

We need business card for a finance company, office based in Hong Kong , our Head office is in US, our business is to Merge and acquires companies , the new office will be a regional office for the Asia Pacific region. We want to use the head office logo as attached ( but don't have to be exactly the same, can be a variation to it) as a base and then add Asia Pacific alongside the logo.
We would prefer to have be bilingual Eng + Chinese, although we don't really have Chinese company name .

Industry/Entity Type

Business

Contact Information for Business Card

Clara Jo Tsang
 

VP,
APAC M&A Operations
Orin Vantage Asia Pacific Limited
 
Unit 1407, K18
18 Tai Lok Shan Road, 
Hong Kong 
 
M: +852 6038 1742
T : +852 2836 4100
F : +852 2836 4177
VOIP: 4158
 
cjtsang@orinvantage.com

Font styles to use
Serif
Sans Serif

Colors

Designer to choose colors to be used in the design.

Requirements
Must have
• APAC Office

```html
<!DOCTYPE html>
<html lang="en">
<head>
<meta charset="utf-8">
<title>Orin Vantage – Business Card</title>
<link href="https://fonts.googleapis.com/css2?family=Open+Sans:wght@700&family=Roboto:wght@400;500&family=Roboto+Condensed:wght@500&display=swap" rel="stylesheet">
<style>
  :root {
    --backdrop: #2b2b2b;
    --navy: #0f2942;
    --cyan: #1fadd1;
    --text-light: #e6ebf0;
  }
  * { margin: 0; padding: 0; box-sizing: border-box; }
  html, body {
    width: 1200px; height: 960px; overflow: hidden;
    background: var(--backdrop);
  }
  .canvas { position: relative; width: 1200px; height: 960px; }

  .card {
    position: absolute;
    width: 600px;
    background: var(--navy);
    overflow: hidden;
    color: var(--text-light);
    font-family: "Roboto", Arial, sans-serif;
  }

  /* Front */
  .card--front { left: 322px; top: 108px; height: 336px; }
  .brand-mark {
    position: absolute; left: 286px; top: 96px;
    width: 28px; height: 28px;
    background: var(--text-light);
  }
  .brand-name {
    position: absolute; left: 0; right: 0; top: 184px;
    text-align: center;
    font-family: "Open Sans", Arial, sans-serif;
    font-weight: 700; font-size: 50px; letter-spacing: -0.5px;
    color: var(--cyan); line-height: 1;
  }
  .brand-web {
    position: absolute; left: 0; right: 0; top: 284px;
    text-align: center;
    font-size: 14px; letter-spacing: 5.2px;
    color: var(--text-light);
  }

  /* Back */
  .card--back { left: 320px; top: 492px; height: 343px; }
  .accent-band { position: absolute; right: 0; top: 0; }
  .holder-name {
    position: absolute; left: 34px; top: 24px;
    font-family: "Roboto Condensed", Arial, sans-serif;
    font-weight: 500; font-size: 21px; color: var(--cyan);
  }
  .holder-title {
    position: absolute; left: 36px; top: 52px;
    font-weight: 500; font-size: 14px;
  }
  .office-address {
    position: absolute; left: 35px; top: 126px;
    font-size: 14.5px; line-height: 19px; font-style: normal;
  }
  .contact-list {
    position: absolute; left: 35px; top: 227px;
    list-style: none; font-size: 14.5px; line-height: 19px;
  }
  .contact-list li { display: flex; align-items: center; gap: 9px; }
  .contact-list svg { width: 14px; height: 14px; fill: var(--cyan); }
  .voip {
    position: absolute; left: 35px; top: 293px; font-size: 14.5px;
  }
</style>
</head>
<body>
<main class="canvas">

  <section class="card card--front">
    <span class="brand-mark"></span>
    <h1 class="brand-name">ORIN VANTAGE</h1>
    <p class="brand-web">www.orinvantage.com</p>
  </section>

  <section class="card card--back">
    <svg class="accent-band" width="600" height="343" viewBox="0 0 600 343">
      <polygon points="430,0 600,0 600,170" fill="var(--cyan)"/>
      <polygon points="600,170 600,343 430,343" fill="var(--cyan)"/>
    </svg>

    <h2 class="holder-name">CLARA JO TSANG</h2>
    <p class="holder-title">VP</p>

    <address class="office-address">
      APAC M&amp;A Operations<br>
      Orin Vantage Asia Pacific Limited<br>
      Unit 1407, K18<br>
      18 Tai Lok Shan Road<br>
      Hong Kong
    </address>

    <ul class="contact-list">
      <li>
        <svg viewBox="0 0 24 24" aria-label="Telephone"><path d="M6.6 10.8a15.1 15.1 0 0 0 6.6 6.6l2.2-2.2c.3-.3.7-.4 1-.2 1.1.4 2.3.6 3.6.6.6 0 1 .4 1 1V20c0 .6-.4 1-1 1A17 17 0 0 1 3 4c0-.6.4-1 1-1h3.5c.6 0 1 .4 1 1 0 1.3.2 2.5.6 3.6.1.3 0 .7-.2 1z"/></svg>
        +852 2836 4100
      </li>
      <li>
        <svg viewBox="0 0 24 24" aria-label="Mobile"><path d="M7 1h10a2 2 0 0 1 2 2v18a2 2 0 0 1-2 2H7a2 2 0 0 1-2-2V3a2 2 0 0 1 2-2zm0 3v15h10V4zm5 16.2a1 1 0 1 0 0 2 1 1 0 0 0 0-2z"/></svg>
        +852 6038 1742
      </li>
      <li>
        <svg viewBox="0 0 24 24" aria-label="Fax"><path d="M6 2h9l3 3v4H6zM3 10h18a2 2 0 0 1 2 2v7a2 2 0 0 1-2 2H3a2 2 0 0 1-2-2v-7a2 2 0 0 1 2-2zm3 4v2h12v-2z"/></svg>
        +852 2836 4177
      </li>
    </ul>

    <p class="voip">VOIP: 4158</p>
  </section>

</main>
</body>
</html>
```